Autobiography cover

Mathis Duverbec: "What lies past the door?", Editions Morvane. The book covers the life of a man (the author) who made a career in a big hospital. Size of the book: 16 x 24 cm

Target Market(s)

General public

Colors

Designer to choose colors to be used in the design.

Requirements
Must have
• A white coat doctor facing a corridor of an hospital. The name of the author (Mathis Duverbec) at the top of the page The publisher (Morvane Editions) in Gill Sans light at the bottom

```html
<!DOCTYPE html>
<html lang="en">
<head>
<meta charset="utf-8">
<title>What lies past the door? — Mathis Duverbec</title>
<link rel="stylesheet" href="https://fonts.googleapis.com/css2?family=Lato:wght@300&family=Tinos:wght@400;700&display=swap">
<style>
  :root {
    --page: #ffffff;
    --corridor-light: #e9f1f8;
    --corridor-mid: #bcd2e4;
    --corridor-deep: #8eaecb;
    --coat-light: #f7f9fb;
    --coat-shade: #dfe6ee;
    --title-blue: #1a5db0;
    --ink: #0b0b0b;
  }
  html, body {
    margin: 0;
    padding: 0;
    width: 1200px;
    height: 1200px;
    overflow: hidden;
    background: var(--page);
  }
  .cover {
    position: absolute;
    left: 213px;
    top: 20px;
    width: 775px;
    height: 1160px;
    overflow: hidden;
    font-family: "Tinos", "Times New Roman", serif;
  }
  .cover-photo {
    position: absolute;
    inset: 0;
    background:
      radial-gradient(ellipse 60% 45% at 62% 62%, var(--corridor-light) 0%, rgba(233,241,248,0) 100%),
      linear-gradient(180deg, var(--corridor-mid) 0%, var(--corridor-deep) 45%, var(--corridor-mid) 75%, var(--corridor-light) 100%);
  }
  .cover-photo .figure-zone {
    position: absolute;
    left: 0;
    top: 190px;
    width: 420px;
    bottom: 0;
    border-radius: 180px 180px 0 0;
    background: linear-gradient(90deg, var(--coat-light) 0%, var(--coat-light) 70%, var(--coat-shade) 100%);
  }
  .author {
    position: absolute;
    top: 36px;
    left: 0;
    right: 0;
    margin: 0;
    text-align: center;
    font-weight: 700;
    font-size: 58px;
    letter-spacing: 0.5px;
    color: var(--ink);
  }
  .title {
    position: absolute;
    top: 381px;
    left: 0;
    right: 0;
    margin: 0;
    text-align: center;
    font-weight: 700;
    font-size: 100px;
    line-height: 120px;
    color: var(--title-blue);
    text-transform: uppercase;
  }
  .title span { display: block; }
  .publisher {
    position: absolute;
    top: 1080px;
    left: 0;
    right: 0;
    margin: 0;
    text-align: center;
    font-family: "Lato", "Gill Sans", sans-serif;
    font-weight: 300;
    font-size: 48px;
    letter-spacing: 1px;
    color: var(--ink);
    text-transform: uppercase;
  }
</style>
</head>
<body>
  <main class="cover">
    <div class="cover-photo" role="img" aria-label="Photograph of a doctor in a white coat seen from behind, hands clasped holding a stethoscope, facing a long bright hospital corridor">
      <div class="figure-zone" aria-hidden="true"></div>
    </div>
    <h2 class="author">MATHIS DUVERBEC</h2>
    <h1 class="title">
      <span>What lies</span>
      <span>past the</span>
      <span>door?</span>
    </h1>
    <p class="publisher">Editions Morvane</p>
  </main>
</body>
</html>
```